Luxury Business Card Design for High-End Window Treatments

Gilded Slatworks
Custom Plantation Shutters & Architectural Shading Systems

⸻

BACK

Daniel Trevick
Owner

Custom Interior & Exterior Window Treatments

919-555-0148
gildedslatworks.com

I have included a picture that I’m hoping we can use on the back, but I’m also wondering if you can get rid of the ladder? Should we get rid of shutters , shades and blinds underneath Gilded Slatworks?

Target Market(s)

High-end residential homeowners, custom home builders, architects, interior designers, and luxury renovation clients seeking premium plantation shutters and motorized architectural shading systems.

Industry/Entity Type

Custom Window treatments

Contact Information for Business Card

Front Gilded Slatworks Custom Plantation Shutters Motorized Architectural Shading Systems BACK Daniel Trevick Owner 919-555-0148 GildedSlatworks.com Custom Interior & Exterior Window Treatments By Appointment

Requirements
Nice to have
• Not 100% sure on nice to halves or the color but you can definitely check out my website to get a better understanding of what I’m trying to do

```html
<!DOCTYPE html>
<html lang="en">
<head>
<meta charset="utf-8">
<title>Gilded Slatworks — Business Card</title>
<link rel="stylesheet" href="https://fonts.googleapis.com/css2?family=Tinos:wght@400;700&family=Sansita:wght@700&display=swap">
<style>
  :root {
    --page: #1c1c1e;
    --card: #050505;
    --gold: #f6d46b;
    --cream: #efe8d8;
    --white: #ffffff;
    --ink: #1a1a1a;
    --sky-top: #3f7fd1;
    --sky-low: #a9c8ea;
    --house: #8d8a84;
    --lawn: #5f6a3e;
  }
  * { box-sizing: border-box; margin: 0; padding: 0; }
  html, body {
    width: 1200px; height: 900px; overflow: hidden;
    background: var(--page);
  }
  .sheet {
    width: 1200px; height: 900px;
    display: flex; flex-direction: column; align-items: center; justify-content: center;
    gap: 36px;
  }
  .card {
    position: relative;
    width: 700px; height: 400px;
    border-radius: 22px;
    background: var(--card);
    overflow: hidden;
    box-shadow: 0 14px 30px rgba(0,0,0,.55);
  }

  /* Front */
  .front { display: flex; flex-direction: column; align-items: center; padding-top: 70px; }
  .wordmark {
    font-family: "Tinos", serif; font-weight: 400;
    color: var(--cream); font-size: 58px; line-height: 1; letter-spacing: .5px;
  }
  .product-line {
    display: flex; gap: 28px; margin-top: 18px;
    font-family: "Sansita", sans-serif; font-weight: 700;
    color: var(--gold); font-size: 27px; letter-spacing: .5px;
  }
  .services {
    list-style: none; margin-top: 40px; text-align: center;
    font-family: "Tinos", serif; color: var(--white); font-size: 27px; line-height: 1.3;
  }
  .services li::before { content: "•"; margin-right: 12px; }

  /* Back */
  .photo {
    position: absolute; left: 0; top: 0; width: 62%; height: 100%;
    background:
      linear-gradient(90deg, rgba(5,5,5,0) 70%, var(--card) 100%),
      linear-gradient(180deg, var(--sky-top) 0%, var(--sky-low) 30%, var(--house) 48%, #4b4a47 70%, var(--lawn) 100%);
  }
  .details {
    position: absolute; right: 28px; top: 36px; width: 330px;
    display: flex; flex-direction: column; align-items: center;
  }
  .details .wordmark { font-size: 40px; }
  .details .product-line { font-size: 18px; gap: 18px; margin-top: 12px; }
  .contact { align-self: stretch; margin-top: 26px; padding-left: 36px; }
  .person-name {
    font-family: "Tinos", serif; font-weight: 700;
    color: var(--gold); font-size: 32px; line-height: 1.1;
  }
  .person-role {
    font-family: "Tinos", serif; color: var(--white); font-size: 20px; margin: 4px 0 0 26px;
  }
  .contact-row {
    display: flex; align-items: center; gap: 12px;
    font-family: "Tinos", serif; color: var(--white); font-size: 20px;
    margin: 12px 0 0 40px;
  }
  .contact-row svg { width: 20px; height: 20px; flex: none; }
  .tagline-band {
    position: absolute; left: 0; right: 0; bottom: 0; height: 48px;
    background: var(--gold);
    display: flex; align-items: center; justify-content: center;
    font-family: "Tinos", serif; font-weight: 700; color: var(--ink); font-size: 23px;
  }
</style>
</head>
<body>
<main class="sheet">

  <section class="card front" aria-label="Card front">
    <h1 class="wordmark">Gilded Slatworks</h1>
    <p class="product-line"><span>Shutters</span><span>Shades</span><span>Blinds</span></p>
    <ul class="services">
      <li>Custom Plantation Shutters</li>
      <li>Motorized Architectural Shading Systems</li>
    </ul>
  </section>

  <section class="card back" aria-label="Card back">
    <div class="photo" role="img" aria-label="Photo of a two-storey home with screened porches, pine trees, lawn and Adirondack chairs under a blue sky"></div>
    <div class="details">
      <h2 class="wordmark">Gilded Slatworks</h2>
      <p class="product-line"><span>Shutters</span><span>Shades</span><span>Blinds</span></p>
      <div class="contact">
        <p class="person-name">Daniel Trevick</p>
        <p class="person-role">Owner</p>
        <p class="contact-row">
          <svg viewBox="0 0 24 24" aria-hidden="true"><path fill="var(--gold)" d="M6.6 10.8a15.1 15.1 0 0 0 6.6 6.6l2.2-2.2c.3-.3.7-.4 1-.2 1.1.4 2.3.6 3.6.6.6 0 1 .4 1 1V20c0 .6-.4 1-1 1A17 17 0 0 1 3 4c0-.6.4-1 1-1h3.5c.6 0 1 .4 1 1 0 1.3.2 2.5.6 3.6.1.3 0 .7-.2 1z"/></svg>
          919-555-0148
        </p>
        <p class="contact-row">
          <svg viewBox="0 0 24 24" aria-hidden="true"><circle cx="12" cy="12" r="10" fill="var(--gold)"/><path fill="none" stroke="var(--card)" stroke-width="1.6" d="M2 12h20M12 2c3 3 3 17 0 20M12 2c-3 3-3 17 0 20"/></svg>
          gildedslatworks.com
        </p>
      </div>
    </div>
    <p class="tagline-band">Custom Interior &amp; Exterior Window Treatments By Appointment</p>
  </section>

</main>
</body>
</html>
```